Colin Vardek Business card

Hey there, I’m hoping to have a business card designed. I’m in Real estate and just switched to a new Brokerage called: The Harbourline Property Group

The back could just be the company name maybe or whatever looks good!

I’ve attached some logos of our company and some cards my buddy had done up.

On the card:
Colin Vardek
colinvardek@mailora.com
587-412-9065
colinvardek.ca

Target Market(s)

Home buyers and sellers

Industry/Entity Type

Real Estate

Contact Information for Business Card

just looking for a cool and modern design with my picture on it. I like the idea of Black and red being used.

Requirements
Must have
• all the details provided. I'm open to anything. Just want a professional looking card.

```html
<!DOCTYPE html>
<html lang="en">
<head>
<meta charset="utf-8">
<title>Colin Vardek – Business Card</title>
<link href="https://fonts.googleapis.com/css2?family=Montserrat:wght@700;800&family=Roboto:wght@400;500&display=swap" rel="stylesheet">
<style>
  :root {
    --brand-red: #d01f3a;
    --brand-red-deep: #a8142b;
    --brand-red-bright: #ec1c3b;
    --ink: #1d1d1f;
    --text-grey: #5a5a5e;
    --paper: #ffffff;
    --backdrop: #2a2a2c;
  }
  * { box-sizing: border-box; margin: 0; padding: 0; }
  html, body {
    width: 1200px; height: 852px; overflow: hidden;
    background: var(--backdrop);
  }
  .sheet {
    width: 1200px; height: 852px;
    display: flex; align-items: center; justify-content: center; gap: 44px;
  }
  .card {
    position: relative;
    width: 540px; height: 309px;
    border-radius: 22px;
    overflow: hidden;
    box-shadow: 0 14px 30px rgba(0,0,0,.45);
  }

  /* Front */
  .card--front {
    background: linear-gradient(120deg, var(--brand-red) 0%, var(--brand-red) 55%, var(--brand-red-bright) 100%);
  }
  .card--front .accent-band {
    position: absolute; right: 0; top: 0; width: 190px; height: 100%;
    background: linear-gradient(160deg, var(--brand-red-deep) 0%, rgba(236,28,59,0) 70%);
    opacity: .55;
  }
  .wordmark {
    font-family: "Montserrat", sans-serif;
    font-weight: 800;
    text-transform: uppercase;
    line-height: 1.02;
    letter-spacing: .5px;
  }
  .card--front .wordmark {
    position: absolute; left: 40px; top: 150px;
    color: var(--paper);
    font-size: 25px;
    display: flex; align-items: center; gap: 12px;
  }
  .wordmark .mark-square {
    width: 16px; height: 16px; background: currentColor; flex: none;
  }

  /* Back */
  .card--back {
    background: var(--paper);
    border-bottom: 5px solid var(--brand-red);
  }
  .card--back .portrait {
    position: absolute; right: 0; top: 0; width: 230px; height: 304px;
    background: linear-gradient(180deg, #ffffff 0%, #e9e6e3 35%, #3a3d44 75%, #25272c 100%);
  }
  .card--back .wordmark {
    position: absolute; left: 38px; top: 58px;
    color: var(--ink);
    font-size: 22px;
    width: 260px;
  }
  .edge-tab {
    position: absolute; left: 0; top: 214px; width: 14px; height: 28px;
    background: var(--brand-red);
  }
  .agent-name {
    position: absolute; left: 38px; top: 168px;
    font-family: "Montserrat", sans-serif; font-weight: 700;
    font-size: 21px; color: var(--brand-red);
  }
  .contact-list {
    position: absolute; left: 58px; top: 208px;
    list-style: none;
    font-family: "Roboto", sans-serif; font-weight: 400;
    font-size: 14.5px; color: var(--text-grey);
  }
  .contact-list li {
    display: flex; align-items: center; gap: 8px; height: 22px;
  }
  .contact-list svg { width: 13px; height: 13px; flex: none; }
</style>
</head>
<body>
<main class="sheet">

  <section class="card card--front" aria-label="Card front">
    <div class="accent-band"></div>
    <div class="wordmark"><span class="mark-square"></span><span>The Harbourline<br>Property Group</span></div>
  </section>

  <section class="card card--back" aria-label="Card back">
    <div class="portrait" role="img" aria-label="Portrait photo of Colin Vardek in a dark blazer and white shirt"></div>
    <div class="wordmark">The Harbourline Property Group</div>
    <div class="edge-tab"></div>
    <p class="agent-name">Colin Vardek</p>
    <ul class="contact-list">
      <li>
        <svg viewBox="0 0 16 16"><circle cx="8" cy="8" r="8" fill="#d01f3a"/><path d="M5 4.5l1.6-.4.9 2-1 .8c.5 1.1 1.3 1.9 2.4 2.4l.8-1 2 .9-.4 1.6c-3.6.1-6.4-2.7-6.3-6.3z" fill="#fff"/></svg>
        <span>587-412-9065</span>
      </li>
      <li>
        <svg viewBox="0 0 16 16"><circle cx="8" cy="8" r="8" fill="#d01f3a"/><rect x="4" y="5" width="8" height="6" fill="none" stroke="#fff" stroke-width="1.2"/><path d="M4 5l4 3.3L12 5" fill="none" stroke="#fff" stroke-width="1.2"/></svg>
        <span>colinvardek@mailora.com</span>
      </li>
      <li>
        <svg viewBox="0 0 16 16"><circle cx="8" cy="8" r="8" fill="#d01f3a"/><circle cx="8" cy="8" r="4.2" fill="none" stroke="#fff" stroke-width="1.1"/><path d="M3.8 8h8.4M8 3.8c-2 2.4-2 6 0 8.4M8 3.8c2 2.4 2 6 0 8.4" fill="none" stroke="#fff" stroke-width="1"/></svg>
        <span>colinvardek.ca</span>
      </li>
    </ul>
  </section>

</main>
</body>
</html>
```